Residential & commercial landscaping company

Updated business cards for commercial and landscaping company. We would like to keep out logo, but just need a more updated business card.

```html
<!DOCTYPE html>
<html lang="en">
<head>
<meta charset="utf-8">
<title>GreenReach Business Card</title>
<link rel="stylesheet" href="https://fonts.googleapis.com/css2?family=Arimo:wght@400;700&family=Tinos:wght@700&display=swap">
<style>
  :root {
    --ink: #0a0a0a;
    --paper: #ffffff;
    --leaf: #33cc33;
    --stage: #e6e6e3;
    --text: #1a1a1a;
  }
  * { box-sizing: border-box; margin: 0; padding: 0; }
  html, body { width: 1200px; height: 900px; overflow: hidden; }
  body {
    background: var(--stage);
    font-family: "Arimo", Arial, sans-serif;
    position: relative;
  }
  .card {
    position: absolute;
    left: 250px;
    width: 700px;
    height: 400px;
    overflow: hidden;
    box-shadow: 0 6px 18px rgba(0,0,0,.18);
  }
  .card-back { top: 40px; background: var(--ink); }
  .card-front { top: 460px; background: var(--paper); }

  .brand {
    display: flex;
    align-items: center;
    gap: 14px;
    font-family: "Arimo", Arial, sans-serif;
    font-weight: 700;
    letter-spacing: -1px;
    white-space: nowrap;
  }
  .brand-dot { width: 26px; height: 26px; border-radius: 50%; background: var(--leaf); flex: none; }
  .card-back .brand {
    position: absolute; left: 0; right: 0; top: 160px;
    justify-content: center;
    font-size: 72px; color: var(--paper);
  }
  .card-front .brand {
    position: absolute; right: 36px; top: 74px;
    font-size: 44px; color: var(--ink);
  }
  .card-front .brand-dot { width: 18px; height: 18px; }

  .holder { position: absolute; left: 56px; top: 56px; }
  .holder-name {
    font-family: "Tinos", "Times New Roman", serif;
    font-weight: 700;
    font-size: 34px;
    color: var(--leaf);
    letter-spacing: .5px;
    white-space: nowrap;
  }
  .holder-role { font-size: 20px; color: var(--text); margin-top: 2px; letter-spacing: .5px; }

  .contact-list { position: absolute; left: 80px; top: 172px; list-style: none; }
  .contact-item {
    display: flex; align-items: center; gap: 10px;
    font-size: 19px; color: var(--text); line-height: 30px; letter-spacing: .4px;
    white-space: nowrap;
  }
  .contact-icon { width: 20px; height: 20px; fill: var(--leaf); flex: none; }
  .contact-web {
    position: absolute; left: 330px; top: 136px;
    font-size: 19px; color: var(--text); letter-spacing: .4px; white-space: nowrap;
  }

  .swoosh { position: absolute; inset: 0; width: 700px; height: 400px; }
</style>
</head>
<body>

  <section class="card card-back" aria-label="Card back">
    <div class="brand"><span class="brand-dot"></span>GreenReach</div>
  </section>

  <section class="card card-front" aria-label="Card front">
    <svg class="swoosh" viewBox="0 0 700 400" aria-hidden="true">
      <path fill="var(--leaf)" d="M0,330 C190,336 360,312 505,222 L520,216 C390,318 210,360 0,366 Z"/>
      <path fill="var(--ink)" d="M0,378 C210,372 390,332 535,224 C600,178 650,152 700,142 L700,400 L0,400 Z"/>
    </svg>

    <div class="holder">
      <p class="holder-name">Daniel Hartwell Jr.</p>
      <p class="holder-role">Project Manager</p>
    </div>

    <div class="brand"><span class="brand-dot"></span>GreenReach</div>

    <p class="contact-web">GreenReachLandscapes.com</p>

    <ul class="contact-list">
      <li class="contact-item">
        <svg class="contact-icon" viewBox="0 0 24 24"><path d="M6.6 10.8a15.1 15.1 0 0 0 6.6 6.6l2.2-2.2c.3-.3.7-.4 1-.2 1.1.4 2.3.6 3.6.6.6 0 1 .4 1 1V20c0 .6-.4 1-1 1A17 17 0 0 1 3 4c0-.6.4-1 1-1h3.5c.6 0 1 .4 1 1 0 1.3.2 2.5.6 3.6.1.3 0 .7-.2 1z"/></svg>
        555-214-0370 ext.412
      </li>
      <li class="contact-item">
        <svg class="contact-icon" viewBox="0 0 24 24"><path d="M7 3h10v4H7z"/><path d="M4 8h16a2 2 0 0 1 2 2v6h-4v-3H6v3H2v-6a2 2 0 0 1 2-2z"/><path d="M7 14h10v7H7z"/></svg>
        555-386-4920
      </li>
      <li class="contact-item">
        <svg class="contact-icon" viewBox="0 0 24 24"><path d="M2 5h20v14H2z M4 7v.5l8 5.5 8-5.5V7z" fill-rule="evenodd"/></svg>
        dan@GreenReachLandscapes.com
      </li>
    </ul>
  </section>

</body>
</html>
```